RB Halden Electric Yard Sign

Looking to have a yard sign designed that we can place at projects we are working on. Most likely will be 18" H x 24" W but flexible that we can increase the size if necessary. It should include our logo, our phone # 609-555-0147, website rbhaldenelectric.example and slogan, built on integrity, driven by excellence. Colors should match our brand.

```html
<!DOCTYPE html>
<html lang="en">
<head>
<meta charset="utf-8">
<title>RB Halden Electric Yard Sign</title>
<link href="https://fonts.googleapis.com/css2?family=Montserrat:wght@600;700;800&display=swap" rel="stylesheet">
<style>
  :root {
    --navy: #03356b;
    --red: #e21e2a;
    --white: #ffffff;
    --backdrop: #eceff2;
    --font: "Montserrat", Arial, sans-serif;
  }
  * { margin: 0; padding: 0; box-sizing: border-box; }
  html, body {
    width: 1200px;
    height: 1200px;
    overflow: hidden;
    background: var(--backdrop);
    font-family: var(--font);
  }
  .canvas {
    position: relative;
    width: 1200px;
    height: 1200px;
    display: flex;
    align-items: center;
    justify-content: center;
  }
  .yard-sign {
    position: relative;
    width: 1100px;
    height: 825px;
    background: var(--white);
    overflow: hidden;
    box-shadow: 0 10px 30px rgba(0, 0, 0, 0.15);
  }
  .sign-bands {
    position: absolute;
    inset: 0;
    width: 100%;
    height: 100%;
    display: block;
  }
  .sign-text {
    position: absolute;
    left: 0;
    right: 0;
    text-align: center;
    white-space: nowrap;
  }
  .brand-name {
    top: 145px;
    font-size: 62px;
    font-weight: 800;
    line-height: 76px;
    color: var(--red);
    letter-spacing: 1px;
  }
  .slogan {
    font-size: 72px;
    font-weight: 800;
    line-height: 80px;
  }
  .slogan-integrity { top: 352px; color: var(--red); }
  .slogan-excellence { top: 428px; color: var(--white); font-weight: 700; }
  .phone {
    top: 608px;
    font-size: 128px;
    font-weight: 800;
    line-height: 130px;
    color: var(--white);
    letter-spacing: -1px;
  }
  .website-row {
    top: 736px;
    display: flex;
    align-items: center;
    justify-content: center;
    gap: 18px;
    height: 44px;
  }
  .website-rule {
    width: 190px;
    height: 2px;
    background: var(--white);
  }
  .website {
    font-size: 38px;
    font-weight: 700;
    color: var(--white);
    line-height: 44px;
  }
</style>
</head>
<body>
  <main class="canvas">
    <section class="yard-sign" aria-label="RB Halden Electric yard sign">
      <svg class="sign-bands" viewBox="0 0 1292 968" preserveAspectRatio="none" aria-hidden="true">
        <!-- navy field -->
        <path d="M0 305 Q 646 420 1292 290 L1292 968 L0 968 Z" fill="var(--navy)"/>
        <!-- upper white streak -->
        <path d="M300 340 Q 820 370 1292 318 L1292 342 Q 820 400 300 340 Z" fill="var(--white)"/>
        <!-- upper red swoosh -->
        <path d="M0 318 Q 520 388 1030 386 Q 520 412 0 352 Z" fill="var(--red)"/>
        <!-- lower white streak -->
        <path d="M260 640 Q 800 595 1292 676 L1292 706 Q 800 620 260 640 Z" fill="var(--white)"/>
        <!-- lower red swoosh -->
        <path d="M0 688 Q 500 640 1000 678 Q 500 662 0 708 Z" fill="var(--red)"/>
        <!-- red footer field -->
        <path d="M0 732 Q 620 672 1292 718 L1292 968 L0 968 Z" fill="var(--red)"/>
      </svg>

      <div class="sign-text brand-name">RB Halden Electric</div>

      <div class="sign-text slogan slogan-integrity">Built on Integrity</div>
      <div class="sign-text slogan slogan-excellence">Driven by Excellence</div>

      <div class="sign-text phone">609-555-0147</div>

      <div class="sign-text website-row">
        <span class="website-rule"></span>
        <span class="website">rbhaldenelectric.example</span>
        <span class="website-rule"></span>
      </div>
    </section>
  </main>
</body>
</html>
```